Flyer for Medical practice welcoming new patients

We need a DL size brochure designed for Medical practice to advertise that we are accepting new patients. Our practice has special interests in women's and children's health and seniors health. Our existing advertising materials are in the colour scheme of purples I have uploaded our logo which includes our colour scheme.

Target Market(s)

Versatile to target anyone looking for a small medical practice that offers continuous care of seeing the same Doctor every time

Industry/Entity Type

Advertising

Font styles to use
Serif

Colors
6b449b
876aae
b7a5cc

Requirements
Must have
• The practice logo of just the picture not Dr Petra Holcombe.
• Purple colour scheme.
• Practice name: Tarrabeen Medical Practice.
• Address: 147 Corlett Rd, Tarrabeen NSW 2500.
• Phone: 4871 6035.
• DL size brochure
• Welcoming new patients ( a strong emphasis needs to be placed on this)
• Nurse and onsite ECG's and lung function tests.
• Travel vaccines including yellow fever
• Bulk billing for tertiary students
• We would also like design to alter the text so that we can change the points to be reflect who we are targeting at the time.
Nice to have
• The practice logo with Dr Petra Holcombe somewhere not as a feature as the practice no longer goes under this name but is still well known as Dr Holcombe's.

```html
<!DOCTYPE html>
<html lang="en">
<head>
<meta charset="utf-8">
<title>Tarrabeen Medical Practice – DL Flyer</title>
<link rel="stylesheet" href="https://fonts.googleapis.com/css2?family=Carlito:wght@400;700&family=Open+Sans:wght@400;700&display=swap">
<style>
  :root {
    --purple-deep: #6b449b;
    --purple-mid: #876aae;
    --purple-light: #b7a5cc;
    --purple-text: #5a3590;
    --logo-text: #ece3f6;
    --white: #ffffff;
    --stage: #e4e4e4;
  }
  * { margin: 0; padding: 0; box-sizing: border-box; }
  html, body {
    width: 1200px; height: 1000px; overflow: hidden;
    background: var(--stage);
  }
  .flyer {
    position: absolute; left: 381px; top: 40px;
    width: 438px; height: 920px; overflow: hidden;
    background: var(--white);
  }
  .flyer-shapes { position: absolute; inset: 0; width: 100%; height: 100%; }
  .brand {
    position: absolute; left: 12px; top: 77px;
    display: flex; align-items: center; gap: 36px;
  }
  .brand-mark {
    width: 110px; height: 110px; border-radius: 50%;
    border: 3px solid var(--logo-text);
  }
  .brand-name {
    font-family: "Carlito", sans-serif; font-weight: 400;
    font-size: 29px; line-height: 1.05; color: var(--logo-text);
  }
  .services {
    position: absolute; left: 10px; top: 285px; width: 400px;
    list-style: none;
    font-family: "Carlito", sans-serif; font-size: 23px; line-height: 28px;
    color: var(--purple-text);
  }
  .services li { position: absolute; left: 0; padding-left: 15px; width: 400px; }
  .services li::before {
    content: ""; position: absolute; left: 0; top: 10px;
    width: 10px; height: 10px; border-radius: 50%;
    background: var(--purple-text);
  }
  .services .new-patients { top: 0; }
  .services .nurse { top: 55px; }
  .services .travel { top: 175px; }
  .services .bulk-billing { top: 268px; line-height: 23px; }
  .contact {
    position: absolute; left: 25px; top: 802px;
    font-family: "Open Sans", sans-serif; font-size: 17px; line-height: 26px;
    color: var(--white);
  }
  .contact strong { font-weight: 700; }
  .contact .address-line2 { padding-left: 102px; }
  .contact .phone { margin-top: 18px; padding-left: 8px; }
</style>
</head>
<body>
  <main class="flyer">
    <svg class="flyer-shapes" viewBox="0 0 438 920" aria-hidden="true">
      <defs>
        <linearGradient id="header-fill" x1="0" y1="0" x2="0" y2="1">
          <stop offset="0" stop-color="#8360b0"/>
          <stop offset="1" stop-color="#6b449b"/>
        </linearGradient>
        <linearGradient id="wave-light" x1="0" y1="0" x2="0" y2="1">
          <stop offset="0" stop-color="#c2b2d8"/>
          <stop offset="1" stop-color="#8a6db2"/>
        </linearGradient>
        <linearGradient id="wave-dark" x1="0" y1="0" x2="1" y2="0">
          <stop offset="0" stop-color="#6b449b"/>
          <stop offset="1" stop-color="#9a80c0"/>
        </linearGradient>
        <linearGradient id="footer-fill" x1="0" y1="0" x2="0" y2="1">
          <stop offset="0" stop-color="#b7a5cc"/>
          <stop offset="1" stop-color="#9c83c2"/>
        </linearGradient>
      </defs>
      <path class="header-band" d="M0,0 H438 V130 C330,250 200,270 120,255 C70,245 30,235 0,225 Z" fill="url(#header-fill)"/>
      <ellipse class="header-arc" cx="160" cy="-5" rx="185" ry="68" fill="#b7a5cc"/>
      <path class="wave-light" d="M0,650 C140,640 260,560 438,385 V920 H0 Z" fill="url(#wave-light)"/>
      <path class="wave-dark" d="M0,652 C160,645 300,570 438,505 V920 H0 Z" fill="url(#wave-dark)"/>
      <path class="wave-gap" d="M0,668 C160,660 300,600 438,560 V920 H0 Z" fill="#ffffff"/>
      <path class="footer-band" d="M0,692 C120,660 300,628 438,620 V920 H0 Z" fill="url(#footer-fill)"/>
    </svg>

    <header class="brand">
      <div class="brand-mark"></div>
      <h1 class="brand-name">Tarrabeen<br>Medical Practice</h1>
    </header>

    <ul class="services">
      <li class="new-patients">We are accepting new patients</li>
      <li class="nurse">We have a nurse on site and can<br>&nbsp;do onsite ECG's and lung<br>function tests</li>
      <li class="travel">We offer travel vaccines<br>including yellow fever</li>
      <li class="bulk-billing">Bulk billing for<br>tertiary students</li>
    </ul>

    <footer class="contact">
      <p><strong>Address:</strong> 147 Corlett Rd, Tarrabeen</p>
      <p class="address-line2">NSW 2500.</p>
      <p class="phone"><strong>Telephone:</strong> 4871 6035</p>
    </footer>
  </main>
</body>
</html>
```